Harbourline Electrical Solutions

On one side. LOGO (underneath:) Commercial Industrial Residential

- NAME & CONTACT DETAILS

Marcus T. Hollings
Project Manager

(Cell icon) (441) 555-0187
(Email icon) hlelectricalsolutions@mailvento.com
(Facebook & Instagram icons )@hlelectricalsolutions

Other side: LOGO - underneath ELECTRICAL CONSTRUCTION & MAINTENANCE . LED LIGHTING & AUTOMATION . LIFE SAFETY SYSTEMS (FIRE ALARM / SECURITY) . DATA & COMMUNICATION

```html
<!DOCTYPE html>
<html lang="en">
<head>
<meta charset="utf-8">
<title>Harbourline Electrical Solutions — Business Card</title>
<link href="https://fonts.googleapis.com/css2?family=Montserrat:wght@300;400;500;700&display=swap" rel="stylesheet">
<style>
  :root {
    --backdrop: #29292b;
    --teal: #11566b;
    --teal-deep: #0c4858;
    --ink: #3a3a3c;
    --paper: #ffffff;
    --on-teal: #f2f6f7;
  }
  * { box-sizing: border-box; margin: 0; padding: 0; }
  html, body {
    width: 1200px; height: 1200px; overflow: hidden;
    background: var(--backdrop);
    font-family: "Montserrat", sans-serif;
  }
  .card {
    position: absolute; left: 300px; width: 600px; height: 360px;
  }
  .card-front { top: 225px; background: var(--teal); }
  .card-back { top: 625px; background: var(--paper); }

  .wordmark {
    font-family: "Montserrat", sans-serif;
    font-weight: 400;
    text-transform: uppercase;
    letter-spacing: 0.16em;
    line-height: 1.2;
  }
  .front-wordmark {
    position: absolute; left: 0; right: 0; top: 132px;
    text-align: center; font-size: 22px; color: var(--teal-deep);
  }
  .services {
    position: absolute; left: 0; right: 0; top: 304px;
    text-align: center; color: var(--on-teal);
    font-weight: 300; font-size: 11.2px; line-height: 16px;
    text-transform: uppercase;
  }

  .back-wordmark {
    position: absolute; left: 58px; top: 145px; width: 220px;
    font-size: 14.5px; color: var(--teal);
  }
  .divider {
    position: absolute; left: 294px; top: 131px; width: 1.5px; height: 97px;
    background: var(--teal);
  }
  .contact {
    position: absolute; left: 309px; top: 130px; color: var(--ink);
  }
  .contact-name {
    font-weight: 700; font-size: 16.5px; color: var(--teal);
    text-transform: uppercase; letter-spacing: 0.01em;
  }
  .contact-role { font-weight: 500; font-size: 11.5px; margin-top: 1px; }
  .contact-list { list-style: none; margin-top: 13px; }
  .contact-list li {
    display: flex; align-items: center; gap: 4px;
    font-size: 12px; letter-spacing: 0.03em; height: 19px;
  }
  .icon { width: 13px; height: 13px; flex: none; }
  .social-dot {
    width: 12px; height: 12px; border: 1.2px solid var(--teal);
    border-radius: 50%; flex: none; margin-right: 3px;
  }
</style>
</head>
<body>
  <section class="card card-front">
    <div class="wordmark front-wordmark">Harbourline<br>Electrical<br>Solutions</div>
    <p class="services">
      Electrical Construction &amp; Maintenance • LED Lighting &amp; Automation<br>
      • Life Safety Systems (Fire Alarm / Security) • Data &amp; Communication
    </p>
  </section>

  <section class="card card-back">
    <div class="wordmark back-wordmark">Harbourline<br>Electrical<br>Solutions</div>
    <div class="divider"></div>
    <div class="contact">
      <h1 class="contact-name">Marcus T. Hollings</h1>
      <p class="contact-role">Project Manager</p>
      <ul class="contact-list">
        <li>
          <svg class="icon" viewBox="0 0 16 16" aria-hidden="true">
            <circle cx="8" cy="8" r="7" fill="none" stroke="#11566b" stroke-width="1.2"/>
            <path d="M5.2 4.6l1.3-.3.8 1.8-.8.7a5 5 0 0 0 2.7 2.7l.7-.8 1.8.8-.3 1.3c-3.3.3-6.5-2.9-6.2-6.2z" fill="#11566b"/>
          </svg>
          (441) 555-0187
        </li>
        <li>
          <svg class="icon" viewBox="0 0 16 16" aria-hidden="true">
            <circle cx="8" cy="8" r="7" fill="none" stroke="#11566b" stroke-width="1.2"/>
            <rect x="4.3" y="5.3" width="7.4" height="5.4" fill="none" stroke="#11566b" stroke-width="1"/>
            <path d="M4.3 5.5L8 8.4l3.7-2.9" fill="none" stroke="#11566b" stroke-width="1"/>
          </svg>
          hlelectricalsolutions@mailvento.com
        </li>
        <li>
          <span class="social-dot"></span><span class="social-dot"></span>
          @hlelectricalsolutions
        </li>
      </ul>
    </div>
  </section>
</body>
</html>
```